The logo name is "Harbor Skin". The name of the product will be "Cutaneous Comfort". This product is specifically formulated for amputees. Therefore under the product name it should state "for amputees". The catch phrase will be "Experience Harbor find Calmness"
These are the things we need on the label:
Logo, product name, "for amputees", "Experience Harbor find Calmness", Safe, Effective, Directions: spray on problem areas, no need to dry off. harborskin.example, Made in Canada, 500ml.
The MOST IMPORTANT and therefore the most prominent thing on this lable will be the LOGO! The second most prominent thing will be the word "Comfort" We want to keep it very plain, very simple, very unclutered. Keep in mind that this lable will be placed on a white bottle or have a white back ground. The 500ml white PE bottle with trigger sprayer will have a tear drop label. See attached die line (S-294).
We want to stay with the colours that goes with the colour scheme of the logo. See attached logo. Soft colours. We do not want a picture! We would like the lable to be classy and rich.
Updates
The logo name is "Harbor Skin". The name of the product will be "Cutaneous Comfort". This product is specificlly formulated for amputees. Therefore under the product name it should state "for amputees". The catch phrase will be "Experience Harbor find Calmness"
Logo, product name, "for amputees", catch phrase "Experience Harbor find Calmness", Clean, Safe, Effective, Directions: spray on problem areas, no need to dry off. Also Harbor Skin Corpation, harborskin.example, Made in Canada, 500ml.
We want to stay with the colour scheme of the logo. See attached logo. Soft colours. We do not want a picture! We would like the lable to be classy and rich.
This is the offical directive that came from the governing panal of this lable. This panal it not know where it wanted to take this lable that would represent this line until they review all of your submissions, thank you for all your talented hard work. But now it is clear it is time to regroup and hit this objective.
Project Deadline Extended
Reason: New restrictions on lable wording for this product.
Target Market(s)
Amputees and Parents of.
Industry/Entity Type
Product
Requirements
Must have
- Final product to be in a pdf or an illustrator file

```html
<!DOCTYPE html>
<html lang="en">
<head>
<meta charset="utf-8">
<title>Harbor Skin – Cutaneous Comfort Label</title>
<link href="https://fonts.googleapis.com/css2?family=Montserrat:wght@600;700;800&family=Open+Sans:wght@600;700&family=Oswald:wght@500&display=swap" rel="stylesheet">
<style>
  :root{
    --canvas:#ffffff;
    --die-line:#a9a9a9;
    --mint:#9ad4c2;
    --peach:#fcd497;
    --teal:#1f8a74;
    --forest:#0f3b2c;
    --orange:#f7941d;
    --ink:#1b1b1b;
  }
  html,body{margin:0;padding:0;overflow:hidden;background:var(--canvas);}
  .artboard{position:relative;width:1200px;height:900px;overflow:hidden;background:var(--canvas);}
  .label-shape{position:absolute;left:0;top:0;}
  .text{position:absolute;margin:0;}
  .brand{left:490px;top:368px;width:270px;display:flex;align-items:center;gap:12px;}
  .brand-mark{width:58px;height:58px;background:var(--teal);flex:none;}
  .brand-name{font-family:"Montserrat",sans-serif;font-weight:700;font-size:34px;line-height:1.05;color:var(--forest);}
  .product-line{left:417px;width:400px;text-align:center;font-family:"Montserrat",sans-serif;}
  .product-first{top:482px;font-weight:700;font-size:34px;color:var(--teal);letter-spacing:-.5px;}
  .product-second{top:518px;font-weight:800;font-size:52px;color:var(--forest);letter-spacing:1px;}
  .audience{left:527px;top:577px;width:176px;height:30px;border-radius:50%;background:var(--orange);
    box-shadow:0 0 0 2px #fff;color:#fff;font-family:"Montserrat",sans-serif;font-weight:700;font-size:17px;
    display:flex;align-items:center;justify-content:center;}
  .tagline{left:417px;top:620px;width:400px;text-align:center;font-family:"Montserrat",sans-serif;
    font-weight:700;font-size:16.5px;line-height:20px;color:var(--teal);}
  .small{font-family:"Open Sans",sans-serif;font-weight:700;font-size:7.5px;line-height:9.5px;color:var(--ink);}
  .directions{left:462px;top:699px;}
  .directions span{font-weight:600;}
  .volume{left:585px;top:702px;font-family:"Oswald",sans-serif;font-weight:500;font-size:14px;color:var(--ink);}
  .company{left:656px;top:699px;}
  .company .origin{display:block;margin-top:6px;}
  .view-caption{left:0;width:1208px;top:779px;text-align:center;font-family:"Open Sans",sans-serif;font-weight:700;font-size:14px;color:var(--ink);}
</style>
</head>
<body>
<main class="artboard">
  <svg class="label-shape" width="1200" height="900" viewBox="0 0 1200 900" aria-hidden="true">
    <defs>
      <clipPath id="teardrop">
        <path d="M668 104 Q690 96 706 126 C738 182 770 330 782 560 L783 722 Q783 752 756 752 L452 752 Q428 752 426 725 C410 600 415 505 460 420 C520 302 600 182 668 104 Z"/>
      </clipPath>
      <path id="arc-top" d="M654 160 A26 26 0 0 1 706 160"/>
      <path id="arc-bottom" d="M648 160 A32 32 0 0 0 712 160"/>
    </defs>
    <g clip-path="url(#teardrop)">
      <rect x="400" y="90" width="400" height="670" fill="#fff"/>
      <path class="top-band" d="M400 90 L800 90 L800 244 C700 240 575 244 535 268 L400 268 Z" fill="var(--mint)"/>
      <path class="bottom-band" d="M418 682 C520 622 640 576 792 612 L792 760 L400 760 Z" fill="var(--peach)"/>
    </g>
    <path d="M668 104 Q690 96 706 126 C738 182 770 330 782 560 L783 722 Q783 752 756 752 L452 752 Q428 752 426 725 C410 600 415 505 460 420 C520 302 600 182 668 104 Z" fill="none" stroke="var(--die-line)" stroke-width="1"/>
    <g class="claim-badge">
      <circle cx="680" cy="163" r="17" fill="#fff" stroke="var(--forest)" stroke-width="3"/>
      <path d="M671 163 L678 170 L692 154" fill="none" stroke="var(--forest)" stroke-width="4" stroke-linecap="round" stroke-linejoin="round"/>
      <text font-family="Montserrat,sans-serif" font-weight="800" font-size="11" fill="var(--forest)">
        <textPath href="#arc-top" startOffset="50%" text-anchor="middle">Safe</textPath>
      </text>
      <text font-family="Montserrat,sans-serif" font-weight="800" font-size="11" fill="var(--forest)" dy="9">
        <textPath href="#arc-bottom" startOffset="50%" text-anchor="middle">Effective</textPath>
      </text>
    </g>
  </svg>

  <div class="text brand">
    <span class="brand-mark"></span>
    <span class="brand-name">Harbor Skin</span>
  </div>

  <p class="text product-line product-first">Cutaneous</p>
  <p class="text product-line product-second">COMFORT</p>
  <p class="text audience">For Amputees</p>
  <p class="text tagline">Experience Harbor<br>Find Calmness</p>

  <p class="text small directions">DIRECTIONS:<br><span>Spray on problem areas,<br>no need to dry off.</span></p>
  <p class="text volume">500mL</p>
  <p class="text small company">Harbor Skin Corporation<br><span>www.harborskin.example</span><span class="origin">MADE IN CANADA</span></p>

  <p class="text view-caption">Front</p>
</main>
</body>
</html>
```